Brightline Energy Product Distribution Brochure

We are looking to have our current brochure for our customers completely redesigned...the idea is to present the relevant information in an attractive way . Our website is brightlineenergyco.example where you can find more information about us. We have included a file with a rough idea of the page order and what each should include but feel free to adapt based on design. The example provided is only for context and doesnt have to be maintained. We will be using the brochure both digitally and in print form. As long as it reads easily and is eye catching, the design can be horizontal or vertical.Final deliverable should be indesign file.

"Our Brands" page: should be limited to one page (space being enough) where it has the header for each one (for example diesel generators) space for one or two lines of text and then the corresponding logos for each of the five categories
Updates

For those asking: the "our brands" page should be a single page layout where there is a header with the corresponding section and space for maybe one line of text followed by the two logos for that category. Each of the product pages should be similar in fashion to the one in the document attached: a photo of the product with some white space and space for the text to be included. We will be posting additional examples today

Target Market(s)

We want to present it to customers both digitally and in print so they can see our products

Industry/Entity Type

Power Generation

Font styles to use
Serif

Requirements
Must have
• Eye catching and able to present the information in a presentable fashion. Rest is up to you.
Nice to have
• Should incorporate the colors of our logo but can also add other depending on design

```html
<!DOCTYPE html>
<html lang="en">
<head>
<meta charset="utf-8">
<title>Brightline Energy – Distributor Program Guide</title>
<link rel="stylesheet" href="https://fonts.googleapis.com/css2?family=Montserrat:wght@400;800&family=Exo+2:wght@200&display=swap">
<style>
  :root {
    --bg: #c9c9c9;
    --paper: #ffffff;
    --gold: #f6c400;
    --charcoal: #4a4546;
    --text-grey: #5b5b5b;
    --white: #ffffff;
  }
  * { margin: 0; padding: 0; box-sizing: border-box; }
  html, body { width: 1200px; height: 857px; overflow: hidden; }
  body { background: var(--bg); position: relative; }
  .cover {
    position: absolute; left: 310px; top: 28px;
    width: 580px; height: 800px;
    background: var(--paper);
    box-shadow: 0 6px 24px rgba(0,0,0,.18);
    overflow: hidden;
  }
  .cover-art { position: absolute; inset: 0; }
  .title {
    position: absolute; left: 40px; top: 78px;
    font-family: "Montserrat", sans-serif; font-weight: 800;
    font-size: 44px; line-height: 1.04; color: var(--white);
    letter-spacing: .5px; text-shadow: 0 2px 6px rgba(0,0,0,.35);
  }
  .title-rule {
    position: absolute; left: 40px; top: 186px;
    width: 58px; height: 1px; background: var(--white);
  }
  .subtitle {
    position: absolute; left: 40px; top: 200px;
    font-family: "Exo 2", sans-serif; font-weight: 200;
    font-size: 27px; line-height: 1.3; color: var(--white);
    letter-spacing: .5px;
  }
  .address {
    position: absolute; left: 30px; top: 716px;
    font-family: "Montserrat", sans-serif; font-style: normal; font-weight: 400;
    font-size: 10px; line-height: 1.45; color: var(--text-grey);
  }
  .address .phone { color: var(--gold); font-weight: 800; margin-top: 5px; display: block; }
  .brand {
    position: absolute; right: 34px; top: 748px;
    display: flex; align-items: center; gap: 10px;
    font-family: "Montserrat", sans-serif; font-weight: 800;
    font-size: 20px; color: var(--charcoal); letter-spacing: 1px;
  }
  .brand-square { width: 20px; height: 20px; background: var(--gold); }
</style>
</head>
<body>
  <main class="cover">
    <svg class="cover-art" viewBox="0 0 580 800" width="580" height="800">
      <defs>
        <linearGradient id="industrialTone" x1="0" y1="0" x2="1" y2="1">
          <stop offset="0" stop-color="#c9a21c"/>
          <stop offset=".45" stop-color="#7a5a14"/>
          <stop offset="1" stop-color="#3b2e16"/>
        </linearGradient>
        <linearGradient id="machineTone" x1="0" y1="0" x2="1" y2="1">
          <stop offset="0" stop-color="#b9c6d3"/>
          <stop offset="1" stop-color="#4e6176"/>
        </linearGradient>
      </defs>
      <polygon class="hero-photo" role="img" aria-label="Industrial steel plant lit at dusk in golden tones"
        points="0,0 580,0 580,360 215,665 0,400" fill="url(#industrialTone)"/>
      <polygon class="band-charcoal" points="0,400 215,665 580,360 580,382 215,687 0,422" fill="var(--charcoal)"/>
      <polygon class="band-gold" points="0,445 235,735 580,445 580,468 235,758 0,468" fill="var(--gold)"/>
      <g class="inset-photo" role="img" aria-label="Engineers beside generator pipework">
        <polygon points="290,540 350,600 290,660 230,600" fill="url(#machineTone)"/>
      </g>
      <g class="inset-photo" role="img" aria-label="Close-up of a diesel generator engine">
        <polygon points="400,455 460,515 400,575 340,515" fill="url(#machineTone)"/>
      </g>
    </svg>

    <h1 class="title">DISTRIBUTOR<br>PROGRAM GUIDE</h1>
    <div class="title-rule"></div>
    <p class="subtitle">DIESEL GENERATORS<br>ALTERNATORS &amp; PARTS</p>

    <address class="address">
      Brightline Energy Limited, Inc.<br>
      4410 Kestrel Mill Road<br>
      Reno, NV 89502, USA
      <span class="phone">1-800-555-0142</span>
    </address>

    <div class="brand"><span class="brand-square"></span>BRIGHTLINE ENERGY</div>
  </main>
</body>
</html>
```